Association qui souhaite améliorer l'accès aux personnes en situation de handicap

Nous sommes une association qui a pour objectif d'améliorer l'accessibilité, augmenter l'offre des activités réalisables dans notre région touristique.
Nous souhaitons réaliser un site internet afin de pouvoir communiquer sur notre association. Nous avons déjà conçu notre flyer sur Plumotrix. Nous souhaiterions une base graphique se rapportant à celui-ci. C'est possible de tout retravailler mais nous souhaitons tout de même retrouver la charte graphique ou code couleur du flyer.
Il nous faudrait quelques pages:
- 1 page : Acceuil / Présentation (Home), Il y aurait le descriptif de l'association, avec ses objectifs à +/- moyen terme
- 1 page : Nos réalisations, celle-ci présenterait les éléments que nous avons réalisés avec des zones de textes et des images classées chronologiquement au fur et à mesure des nouveautés
- 1 page : Media, comme la précédente, mais ou on pourrait voir ou lire sur les divers médias qui parlent de nous
- 1 page : Evenements : c'est une page pour présenter divers activités que nous allons organiser
- 1 page : Contact qui indique comment nous contacter et avec la présentation des 5 ou 6 membres du comité
- 1 link donate : qui arrive sur un formulaire de donnée que l'on pourra faire évoluer sur un système de payement par la suite. Cette bannière doit se retrouver sur toutes les pages
Il est nécessaire que se design puisse être transféré sur une lecture sur téléphone mobile
Personnes en situation de handicap
Associatif

```html
<!DOCTYPE html>
<html lang="en">
<head>
<meta charset="utf-8">
<title>Openway Association</title>
<link rel="stylesheet" href="https://fonts.googleapis.com/css2?family=Poppins:wght@600;700;800&family=Raleway:wght@400;500;600;700&display=swap">
<style>
:root{
  --red:#e8391e;
  --deep-red:#c41e2a;
  --ink:#111111;
  --text:#333333;
  --pink:#fbecec;
  --mist:#f4f4f4;
  --stone:#d2d2d2;
  --night:#232323;
  --white:#ffffff;
}
*{margin:0;padding:0;box-sizing:border-box}
html,body{width:1200px;height:3842px;overflow:hidden;background:var(--white)}
body{position:relative;font-family:"Raleway",sans-serif;color:var(--text)}
.abs{position:absolute}
.heading{font-family:"Poppins",sans-serif;font-weight:800;color:var(--ink);font-size:26px;letter-spacing:-.3px;text-transform:uppercase}
.rule{position:absolute;height:3px;width:84px;background:var(--red)}
.btn{position:absolute;display:flex;align-items:center;justify-content:center;background:var(--red);color:var(--white);font-family:"Poppins",sans-serif;font-weight:700;font-size:12px;text-transform:uppercase;text-decoration:none}
.para{font-size:14.5px;line-height:21.6px;text-align:justify}
.list{list-style:none}
.list li{position:relative;padding-left:22px;font-size:14.5px;line-height:21.6px;margin-bottom:20px;text-align:justify}
.list li::before{content:"";position:absolute;left:2px;top:7px;width:6px;height:6px;border-top:2px solid var(--red);border-right:2px solid var(--red);transform:rotate(45deg)}
.list.plain li{text-align:left;margin-bottom:19px}
.photo{position:absolute}
/* header */
.brand{position:absolute;display:flex;align-items:center;gap:10px;font-family:"Poppins",sans-serif;font-weight:800;font-size:23px;line-height:26px;text-transform:uppercase}
.brand-mark{width:22px;height:22px;background:var(--deep-red)}
.site-header .brand{left:133px;top:22px;color:var(--ink)}
.top-donate{left:565px;top:18px;width:90px;height:30px;font-size:14px}
.follow{position:absolute;font-size:11px;font-weight:700;color:var(--ink);text-transform:uppercase}
.dot{position:absolute;width:26px;height:26px;border-radius:50%}
.call-label{left:933px;top:17px;font-size:11px;font-weight:700;color:var(--ink)}
.call-number{left:933px;top:32px;font-family:"Poppins",sans-serif;font-size:17px;font-weight:700;color:var(--ink)}
.main-nav a{position:absolute;top:64px;font-size:14px;font-weight:600;color:var(--ink);text-decoration:none;text-transform:uppercase}
.main-nav a.active{color:var(--red)}
/* hero */
.hero{left:0;top:93px;width:1200px;height:650px;background:linear-gradient(180deg,#6fa4d6 0%,#a9c3d8 30%,#8e9298 55%,#b7b2ab 100%)}
.hero-welcome{left:195px;top:278px;font-family:"Poppins",sans-serif;font-weight:800;font-size:24px;color:var(--white)}
.hero-title{left:193px;top:316px;font-family:"Poppins",sans-serif;font-weight:800;font-size:51px;line-height:64px;color:var(--white);letter-spacing:-.5px}
.hero-donate{left:201px;top:462px;width:144px;height:55px;font-size:20px}
/* association visual */
.association-visual{left:131px;top:686px;width:459px;height:562px;background:linear-gradient(135deg,#c41e2a 0%,#e7c9bf 45%,#f3ece6 75%,#e8391e 100%)}
/* cards */
.card{position:absolute;top:2003px;width:290px;height:407px;border:1px solid #e3e3e3;background:var(--white)}
.card .photo{left:0;top:0;width:288px;height:182px}
.card h3{position:absolute;left:25px;top:202px;width:250px;font-size:16px;line-height:21px;font-weight:700;color:var(--ink)}
.card p{position:absolute;left:25px;top:258px;width:235px;font-size:12px;line-height:17.5px}
.card .btn{left:26px;top:343px;width:101px;height:36px}
/* footer */
.site-footer .brand{left:130px;top:3636px;color:var(--white)}
.foot-nav{position:absolute;top:3690px;left:540px;display:flex;height:40px;align-items:center}
.foot-nav a{color:var(--white);text-decoration:none;font-size:14.5px;text-transform:uppercase;padding:0 20px;border-left:1px solid #777;line-height:40px}
.foot-nav a:first-child{border-left:none}
</style>
</head>
<body>

<header class="site-header">
  <div class="brand"><span class="brand-mark"></span><span>Openway<br>Association</span></div>
  <a class="btn top-donate" href="#">Donate</a>
  <span class="follow" style="left:688px;top:26px">Follow us</span>
  <span class="dot" style="left:771px;top:19px;background:#3b5998"></span>
  <span class="dot" style="left:809px;top:19px;background:#444"></span>
  <span class="dot" style="left:847px;top:19px;background:#1da1f2"></span>
  <svg class="abs" style="left:897px;top:19px" width="26" height="26" viewBox="0 0 26 26" aria-hidden="true">
    <circle cx="13" cy="13" r="13" fill="var(--red)"/>
    <path d="M8.5 7.5c.6-.6 1.4-.5 1.8.1l1.3 1.9c.3.5.2 1.1-.2 1.5l-.8.7c.8 1.6 2 2.8 3.6 3.6l.7-.8c.4-.4 1-.5 1.5-.2l1.9 1.3c.6.4.7 1.2.1 1.8l-.9.9c-3.800.6-9.4-5-8.8-8.8z" fill="#fff"/>
  </svg>
  <span class="abs call-label">CALL US</span>
  <span class="abs call-number">+1 555 010 2040</span>
  <nav class="main-nav">
    <a class="active" href="#" style="left:566px">Home</a>
    <a href="#" style="left:638px">Our Achievements</a>
    <a href="#" style="left:823px">Media</a>
    <a href="#" style="left:910px">Events</a>
    <a href="#" style="left:1005px">Contact</a>
  </nav>
</header>

<section class="hero-section">
  <div class="photo hero" role="img" aria-label="Man in a wheelchair on a city square in front of historic buildings"></div>
  <svg class="abs" style="left:0;top:600px" width="1200" height="145" viewBox="0 600 1200 145" aria-hidden="true">
    <polygon points="0,638 745,736 1200,618 1200,745 0,745" fill="#fff"/>
    <polygon points="745,738 1200,618 1200,655" fill="var(--red)"/>
  </svg>
  <svg class="abs" style="left:60px;top:355px" width="30" height="46" viewBox="0 0 30 46" aria-hidden="true"><path d="M24 4 6 23l18 19" stroke="#fff" stroke-width="5" fill="none"/></svg>
  <svg class="abs" style="left:1104px;top:355px" width="30" height="46" viewBox="0 0 30 46" aria-hidden="true"><path d="M6 4l18 19L6 42" stroke="#fff" stroke-width="5" fill="none"/></svg>
  <div class="abs hero-welcome">WELCOME TO</div>
  <h1 class="abs hero-title">OPENWAY<br>ASSOCIATION</h1>
  <a class="btn hero-donate" href="#">Donate</a>
</section>

<section class="association">
  <div class="photo association-visual" role="img" aria-label="Smiling woman using sign language, shown in a decorative red triangular frame"></div>
  <h2 class="abs heading" style="left:632px;top:814px">Association</h2>
  <div class="rule" style="left:632px;top:861px"></div>
  <p class="abs para" style="left:632px;top:898px;width:433px">Sed ut perspiciatis unde omnis iste natus error sit voluptatem accusantium doloremque laudantium, totam rem aperiam, eaque ipsa quae ab illo inventore veritatis et quasi architecto beatae vitae dicta sunt explicabo. Nemo enim ipsam voluptatem quia voluptas sit aspernatur aut odit aut fugit, sed quia consequuntur magni dolores eos qui ratione voluptatem sequi nesciunt. Neque porro quisquam est, qui dolorem ipsum quia dolor sit amet, consectetur, adipisci velit, sed quia non numquam eius modi tempora incidunt ut labore et dolore magnam aliquam quaerat voluptatem.</p>
  <a class="btn" href="#" style="left:634px;top:1147px;width:101px;height:35px">Read more</a>
</section>

<section class="benefits">
  <svg class="abs" style="left:0;top:1284px" width="1200" height="600" viewBox="0 1284 1200 600" aria-hidden="true">
    <polygon points="0,1284 1200,1284 1200,1760 745,1880 0,1788" fill="var(--pink)"/>
    <polygon points="745,1882 1200,1762 1200,1772" fill="var(--pink)"/>
  </svg>
  <h2 class="abs heading" style="left:151px;top:1317px">Benefits</h2>
  <div class="rule" style="left:151px;top:1351px;width:120px"></div>
  <ul class="abs list" style="left:130px;top:1382px;width:463px">
    <li>Promote the reception and leisure of people with disabilities in the Valmont Peaks region by bringing together the information</li>
    <li>To serve the general interest of people in disability as well as relieve caregivers and companions.</li>
    <li>Allow access to leisure and places like everyone else.</li>
    <li>Translation results Raising awareness and changing social representations, through actions, communications, projects and events touching and involving partners associative, economic, political, media and the general public.</li>
    <li>Promote collaboration with local actors</li>
  </ul>
  <a class="btn" href="#" style="left:154px;top:1705px;width:102px;height:35px">Read more</a>
  <div class="photo" style="left:656px;top:1335px;width:409px;height:420px;background:linear-gradient(160deg,#d9d3cb,#b7aa9c 60%,#8c8b88)" role="img" aria-label="Group of people talking in sign language in a bright room"></div>
</section>

<section class="events">
  <h2 class="abs heading" style="left:0;width:1200px;text-align:center;top:1925px">Events</h2>
  <div class="rule" style="left:552px;top:1961px;width:96px"></div>
  <article class="card" style="left:130px">
    <div class="photo" style="background:linear-gradient(160deg,#8fae6a,#4f7fb4 70%,#c8b49c)" role="img" aria-label="Mother hugging her daughter outdoors"></div>
    <h3>Sed ut perspiciatis unde omnis iste natu</h3>
    <p>But I must explain to you how all this mistaken idea of denouncing pleasure and praising &nbsp;pain was born and I will give you a complete account .</p>
    <a class="btn" href="#">Read more</a>
  </article>
  <article class="card" style="left:453px">
    <div class="photo" style="background:linear-gradient(170deg,#c6b26f,#8a9b60 55%,#6a8f3e)" role="img" aria-label="Man in a wheelchair by a lake with a companion"></div>
    <h3>Sed ut perspiciatis unde omnis iste natu</h3>
    <p>But I must explain to you how all this mistaken idea of denouncing pleasure and praising &nbsp;pain was born and I will give you a complete account .</p>
    <a class="btn" href="#">Read more</a>
  </article>
  <article class="card" style="left:777px">
    <div class="photo" style="background:linear-gradient(160deg,#a9a36a,#d8c7a4 60%,#c77c5f)" role="img" aria-label="Little girl blowing soap bubbles in a park"></div>
    <h3>Sed ut perspiciatis unde omnis iste natu</h3>
    <p>But I must explain to you how all this mistaken idea of denouncing pleasure and praising &nbsp;pain was born and I will give you a complete account .</p>
    <a class="btn" href="#">Read more</a>
  </article>
</section>

<section class="media">
  <div class="abs" style="left:590px;top:2465px;width:610px;height:560px;background:var(--mist)"></div>
  <div class="photo" style="left:0;top:2465px;width:590px;height:560px;background:linear-gradient(150deg,#5b7a3a,#a6b47a 45%,#e6d7a8 75%,#c9b58e)" role="img" aria-label="Man with a white cane walking along a sunny park path"></div>
  <h2 class="abs heading" style="left:655px;top:2541px">Media</h2>
  <div class="rule" style="left:655px;top:2587px"></div>
  <p class="abs para" style="left:655px;top:2622px;width:424px;font-size:14px">At vero eos et accusamus et iusto odio dignissimos ducimus qui blanditiis praesentium voluptatum deleniti atque corrupti quos dolores et quas molestias excepturi sint occaecati cupiditate non provident, similique sunt in culpa qui officia deserunt mollitia animi, id est laborum et dolorum fuga. Et harum quidem rerum facilis est et expedita distinctio. Nam libero tempore, cum soluta nobis est eligendi optio cumque nihil impedit quo minus id quod maxime placeat facere possimus, omnis voluptas assumenda est, omnis dolor repellendus. Temporibus autem quibusdam.</p>
  <a class="btn" href="#" style="left:660px;top:2873px;width:101px;height:35px">Read more</a>
</section>

<section class="services">
  <svg class="abs" style="left:0;top:2900px" width="1200" height="700" viewBox="0 2900 1200 700" aria-hidden="true">
    <polygon points="0,2938 745,3034 1200,2915 1200,3600 0,3600" fill="var(--stone)"/>
    <polygon points="745,3036 1200,2917 1200,2926" fill="#fff"/>
  </svg>
  <h2 class="abs heading" style="left:130px;top:3072px;line-height:37px">Lorem ipsum dolor sit amet<br>consectetur adipisci</h2>
  <div class="rule" style="left:130px;top:3162px"></div>
  <ul class="abs list plain" style="left:130px;top:3200px;width:380px">
    <li>Adapt accessibility to certain places tourist or cultural</li>
    <li>Advise various players in the sector tourism and<br>culture for the reception of people with disabilities</li>
    <li>Provide interpreters for various events</li>
    <li>Creation of a platform bringing together tourist sites,<br>accommodation and activities adapted from the<br>Valmont Peaks</li>
  </ul>
  <a class="btn" href="#" style="left:135px;top:3447px;width:101px;height:35px">Read more</a>
  <div class="photo" style="left:625px;top:3105px;width:485px;height:510px;border-radius:40px 40px 0 0;background:radial-gradient(circle at 50% 45%,#f1c9a7,#e9e2d9 55%,rgba(210,210,210,0))" role="img" aria-label="Child holding up hands painted in bright colours"></div>
</section>

<footer class="site-footer">
  <svg class="abs" style="left:0;top:3540px" width="1200" height="302" viewBox="0 3540 1200 302" aria-hidden="true">
    <polygon points="0,3552 745,3636 1200,3560 1200,3842 0,3842" fill="var(--night)"/>
    <polygon points="745,3638 1200,3540 1200,3580" fill="var(--red)"/>
  </svg>
  <div class="brand"><span class="brand-mark" style="background:var(--red)"></span><span>Openway<br>Association</span></div>
  <nav class="foot-nav">
    <a href="#">Home</a><a href="#">Our Achievements</a><a href="#">Media</a><a href="#">Events</a><a href="#">Contact</a>
  </nav>
  <div class="abs" style="left:130px;top:3762px;width:936px;height:1px;background:#666"></div>
  <span class="abs" style="left:132px;top:3789px;font-size:14.5px;color:#fff;text-transform:uppercase">Follow us</span>
  <span class="dot" style="left:234px;top:3784px;background:#3b5998"></span>
  <span class="dot" style="left:271px;top:3784px;background:#555"></span>
  <span class="dot" style="left:308px;top:3784px;background:#1da1f2"></span>
  <span class="abs" style="left:845px;top:3791px;width:218px;text-align:right;font-size:12px;color:#888">Copyright © 2022 All Rights Reserved</span>
</footer>

</body>
</html>
```